Quiet Harbor Podcast W/ Dr. Lena Marsh

Podcast Cover Art. I am in search of a re-design for my existing podcast. We have over 100 episodes, but I want to change the name to Quiet Harbor Podcast With Dr. Lena Marsh. I'm open to any ideas, and have attached source file image to use. ( note: NO brain images please).

```html
<!DOCTYPE html>
<html lang="en">
<head>
<meta charset="utf-8">
<title>Quiet Harbor Podcast With Dr. Lena Marsh</title>
<link rel="stylesheet" href="https://fonts.googleapis.com/css2?family=Bebas+Neue&family=Montserrat:wght@600&display=swap">
<style>
  :root {
    --deep-red: #6e1207;
    --panel-red: #8a1a0a;
    --frame-white: #ffffff;
    --cream: #f8efe9;
    --coral: #ff6f55;
    --ink: #1d1d1d;
    --portrait-top: #e06a4e;
    --portrait-bottom: #c9472d;
  }
  html, body {
    margin: 0;
    padding: 0;
    width: 1200px;
    height: 1200px;
    overflow: hidden;
    background: var(--deep-red);
  }
  .cover {
    display: block;
    width: 1200px;
    height: 1200px;
  }
  .title-main {
    font-family: "Bebas Neue", "Oswald", sans-serif;
    fill: var(--cream);
  }
  .title-sub {
    font-family: "Bebas Neue", "Oswald", sans-serif;
    fill: var(--coral);
  }
  .host-name {
    font-family: "Montserrat", "Helvetica Neue", Arial, sans-serif;
    font-weight: 600;
    fill: var(--ink);
  }
</style>
</head>
<body>
<svg class="cover" viewBox="0 0 1200 1200" xmlns="http://www.w3.org/2000/svg" aria-labelledby="cover-title">
  <title id="cover-title">Quiet Harbor Podcast With Dr. Lena Marsh</title>
  <defs>
    <radialGradient id="backdrop-glow" cx="50%" cy="45%" r="70%">
      <stop offset="0%" stop-color="#9a200d"/>
      <stop offset="100%" stop-color="#5e0f06"/>
    </radialGradient>
    <radialGradient id="panel-glow" cx="50%" cy="40%" r="65%">
      <stop offset="0%" stop-color="#9c220e"/>
      <stop offset="100%" stop-color="#7a1709"/>
    </radialGradient>
    <linearGradient id="portrait-fill" x1="0" y1="0" x2="0" y2="1">
      <stop offset="0%" stop-color="var(--portrait-top)" stop-opacity="0.55"/>
      <stop offset="100%" stop-color="var(--portrait-bottom)"/>
    </linearGradient>
  </defs>

  <!-- backdrop -->
  <rect class="backdrop" width="1200" height="1200" fill="url(#backdrop-glow)"/>

  <!-- framed panel -->
  <rect class="panel" x="147" y="43" width="907" height="1114" fill="url(#panel-glow)"/>
  <rect class="panel-frame" x="143" y="40" width="915" height="1120" fill="none" stroke="var(--frame-white)" stroke-width="4"/>

  <!-- host portrait area -->
  <rect class="host-portrait" x="354" y="75" width="491" height="508" rx="6"
        fill="url(#portrait-fill)" role="img"
        aria-label="Illustrated portrait of the host in a coral checked blazer and white shirt"/>

  <!-- show title -->
  <text class="title-main" x="224" y="814" font-size="300" textLength="755" lengthAdjust="spacingAndGlyphs">QUIET</text>
  <text class="title-sub" x="224" y="981" font-size="209" textLength="755" lengthAdjust="spacingAndGlyphs">HARBOR</text>

  <!-- host name band -->
  <rect class="name-band" x="147" y="1003" width="907" height="118" fill="var(--cream)"/>
  <text class="host-name" x="253" y="1090" font-size="88" textLength="674" lengthAdjust="spacingAndGlyphs">DR. LENA MARSH</text>
</svg>
</body>
</html>
```